Business card design for Brivo Engineering Tandem

We need a new business card design along with all the necessary to place an order. The company is Brivo Engineering Tandem and we recently updated our logo.

```html
<!DOCTYPE html>
<html lang="en">
<head>
<meta charset="utf-8">
<title>Brivo Engineering Tandem – Business Card</title>
<link rel="stylesheet" href="https://fonts.googleapis.com/css2?family=Kanit:wght@300;400;600&display=swap">
<style>
  :root {
    --backdrop: #3a3b3d;
    --card: #1f1f20;
    --brand-grey: #9a9a9a;
    --brand-yellow: #e6c12a;
    --text-light: #f2f2f2;
    --pattern-light: #c9c9c9;
    --pattern-mid: #5a5a5a;
    --pattern-dark: #0c0c0c;
  }
  * { margin: 0; padding: 0; box-sizing: border-box; }
  html, body {
    width: 1200px; height: 1059px; overflow: hidden;
    background: var(--backdrop);
    font-family: "Kanit", sans-serif;
  }
  .canvas { position: relative; width: 1200px; height: 1059px; }

  .card {
    position: absolute;
    width: 690px; height: 394px;
    border-radius: 22px;
    overflow: hidden;
    box-shadow: 0 10px 24px rgba(0,0,0,.45);
  }
  .card--front { left: 255px; top: 100px; background: var(--card); }
  .card--back { left: 254px; top: 536px; background: var(--pattern-dark); }

  .wordmark {
    position: absolute; left: 0; right: 0; top: 62px;
    display: flex; justify-content: center; align-items: center; gap: 14px;
  }
  .wordmark__square { width: 22px; height: 22px; background: var(--brand-yellow); }
  .wordmark__name {
    color: var(--brand-grey); font-weight: 600; font-size: 44px;
    letter-spacing: 2px; text-transform: uppercase; line-height: 1;
  }

  .person {
    position: absolute; right: 390px; top: 213px; text-align: right;
  }
  .person__name {
    color: var(--brand-yellow); font-weight: 600; font-size: 31px;
    line-height: 1; white-space: nowrap;
  }
  .person__role {
    color: var(--text-light); font-weight: 400; font-size: 16.5px;
    margin-top: 12px; line-height: 1;
  }
  .divider {
    position: absolute; left: 329px; top: 216px; width: 2px; height: 70px;
    background: var(--brand-yellow);
  }
  .contact { position: absolute; left: 356px; top: 210px; list-style: none; }
  .contact__item {
    display: flex; align-items: center; gap: 8px;
    color: var(--text-light); font-size: 17px; font-weight: 400;
    height: 27.5px; white-space: nowrap;
  }
  .contact__icon { width: 15px; height: 15px; fill: var(--brand-yellow); flex: none; }
  .address {
    position: absolute; left: 0; right: 0; top: 338px; text-align: center;
    color: var(--text-light); font-size: 16.5px; font-weight: 400;
  }

  .pattern-field {
    position: absolute; inset: 0;
    background: linear-gradient(135deg, var(--pattern-light) 0%, var(--pattern-mid) 35%, #1a1a1a 60%, var(--pattern-dark) 100%);
  }
  .back-wordmark {
    position: absolute; left: 0; right: 0; top: 178px;
    display: flex; justify-content: center; align-items: center; gap: 10px;
  }
  .back-wordmark__square { width: 14px; height: 14px; background: var(--brand-yellow); }
  .back-wordmark__name {
    color: var(--brand-grey); font-weight: 600; font-size: 26px;
    letter-spacing: 1.5px; text-transform: uppercase; line-height: 1;
  }
</style>
</head>
<body>
<main class="canvas">
  <section class="card card--front" aria-label="Business card front">
    <div class="wordmark">
      <span class="wordmark__square"></span>
      <span class="wordmark__name">Brivo Engineering Tandem</span>
    </div>

    <div class="person">
      <p class="person__name">DANIEL HARPER</p>
      <p class="person__role">Managing Director</p>
    </div>
    <div class="divider"></div>
    <ul class="contact">
      <li class="contact__item">
        <svg class="contact__icon" viewBox="0 0 16 16" aria-hidden="true"><path d="M2 5c0-2 3-3 6-3s6 1 6 3v1.5h-3V5H5v1.5H2z"/><path d="M4 8l1.5-1.5h5L12 8l1 5H3z"/></svg>
        <span>01632 960482</span>
      </li>
      <li class="contact__item">
        <svg class="contact__icon" viewBox="0 0 16 16" aria-hidden="true"><path d="M1 3h14v1.2L8 9 1 4.2z"/><path d="M1 5.8l7 4.8 7-4.8V13H1z"/></svg>
        <span>sales@brivoengineering.co.uk</span>
      </li>
      <li class="contact__item">
        <svg class="contact__icon" viewBox="0 0 16 16" aria-hidden="true"><circle cx="8" cy="8" r="7"/><path d="M5 4c1 1 2 1 2 2s-2 1-2 2 1 2 0 3" stroke="#1f1f20" stroke-width="1.4" fill="none"/><path d="M10 9c1 0 2 1 1.5 2.5" stroke="#1f1f20" stroke-width="1.4" fill="none"/></svg>
        <span>www.brivoengineering.co.uk</span>
      </li>
    </ul>
    <p class="address">Brivo Engineering Tandem 12b Kestrel Way, Hollowford NN99 4QT</p>
  </section>

  <section class="card card--back" aria-label="Business card back">
    <div class="pattern-field" role="img" aria-label="Repeating decorative brand pattern fading from silver to black"></div>
    <div class="back-wordmark">
      <span class="back-wordmark__square"></span>
      <span class="back-wordmark__name">Brivo Engineering Tandem</span>
    </div>
  </section>
</main>
</body>
</html>
```